Kestrel Facilities Business Card Design

We would now like to design business cards with the new Kestrel Facilities logo

Target Market(s)

Professional

Industry/Entity Type

Professional services

Contact Information for Business Card

Employee name, title, phone number, email address, corporate office address and logo.

Font styles to use
Sans Serif

Colors
0054AA
0677BA
7BADD7
CADEEF
E8F1F8

Requirements
Must have
• My logo
Should not have
• any other pictures or images besides my logo

```html
<!DOCTYPE html>
<html lang="en">
<head>
<meta charset="utf-8">
<title>Kestrel Facilities Business Card</title>
<link href="https://fonts.googleapis.com/css2?family=Montserrat:wght@400;500;600;700&display=swap" rel="stylesheet">
<style>
  :root{
    --brand-blue:#3578BF;
    --deep-blue:#0054AA;
    --ink:#1E1E1E;
    --paper:#FFFFFF;
    --stage:#D6D6D6;
    --accent-grey:#9A9A9A;
    --mark-light:#D3D9E1;
  }
  *{margin:0;padding:0;box-sizing:border-box}
  html,body{width:1200px;height:813px;overflow:hidden}
  body{
    background:var(--stage);
    font-family:"Montserrat",Arial,sans-serif;
    display:flex;align-items:center;justify-content:center;gap:40px;
  }
  .card{
    position:relative;width:540px;height:310px;border-radius:22px;overflow:hidden;
  }
  .card--front{background:var(--paper)}
  .card--back{background:var(--brand-blue);display:flex;align-items:center;justify-content:center}

  .front__brand{
    position:absolute;left:40px;top:42px;
    font-weight:700;font-size:28px;color:var(--brand-blue);letter-spacing:.5px;
  }
  .front__corner{
    position:absolute;right:0;top:0;width:42px;height:40px;background:var(--accent-grey);
  }
  .person{position:absolute;left:40px;top:138px}
  .person__name{font-weight:700;font-size:22px;color:var(--brand-blue);letter-spacing:.5px}
  .person__title{font-weight:500;font-size:15px;color:var(--ink);margin-top:6px}
  .divider{position:absolute;left:262px;top:128px;width:1.5px;height:92px;background:var(--brand-blue)}
  .contacts{position:absolute;left:280px;top:128px;list-style:none}
  .contacts li{display:flex;align-items:center;gap:8px;font-size:13.5px;color:var(--ink);height:30px}
  .contacts svg{width:15px;height:15px;flex:none}
  .band{
    position:absolute;left:0;right:0;bottom:0;height:54px;background:var(--brand-blue);
    display:flex;align-items:center;padding-left:40px;
    color:var(--paper);font-size:14px;font-weight:500;
  }
  .back__brand{font-weight:700;font-size:40px;color:var(--mark-light);letter-spacing:.5px}
</style>
</head>
<body>
  <section class="card card--front">
    <div class="front__corner"></div>
    <div class="front__brand">Kestrel Facilities</div>
    <div class="person">
      <div class="person__name">DANA WHITFIELD</div>
      <div class="person__title">Co-Founder</div>
    </div>
    <div class="divider"></div>
    <ul class="contacts">
      <li>
        <svg viewBox="0 0 16 16" aria-hidden="true"><path fill="#3578BF" d="M3.6 1.5l2.2 2.8-1.3 1.6c.9 2 2.4 3.5 4.4 4.4l1.6-1.3 2.8 2.2-1.2 2.3C7 13.2 2.8 9 2.5 3z"/></svg>
        +1 555-014-2273
      </li>
      <li>
        <svg viewBox="0 0 16 16" aria-hidden="true"><rect x="1.5" y="3.5" width="13" height="9" fill="none" stroke="#3578BF" stroke-width="1.6"/><path d="M1.5 3.5l6.5 5 6.5-5" fill="none" stroke="#3578BF" stroke-width="1.6"/></svg>
        info@kestrelfm.com
      </li>
      <li>
        <svg viewBox="0 0 16 16" aria-hidden="true"><circle cx="8" cy="8" r="6.5" fill="none" stroke="#3578BF" stroke-width="1.6"/><path d="M1.5 8h13M8 1.5c-3 3.5-3 9.5 0 13M8 1.5c3 3.5 3 9.5 0 13" fill="none" stroke="#3578BF" stroke-width="1.2"/></svg>
        www.kestrelfm.com
      </li>
    </ul>
    <div class="band">4180 Harbor View Road Suite 210 Ashford 28</div>
  </section>

  <section class="card card--back">
    <div class="back__brand">Kestrel Facilities</div>
  </section>
</body>
</html>
```